SitePress Direct-Booking Website for Bend, Oregon Vacation Rental — $750 Budget
Project Overview

We are looking for a talented SitePress designer/developer to create a clean, professional and inviting direct-booking website for Birch Lantern Retreat, an established short-term vacation rental in Bend, Oregon.

The property is currently successfully listed on Staynest and Hoplo. Our Staynest property has approximately a 4.98-star rating with more than 200 reviews, is an Staynest Visitor Pick, and ranks among the Top 1% of eligible homes.

Project Budget: $750

We will select the designer based on the quality of the initial concept, understanding of the property, proposed booking solution and ability to deliver a completed and functioning SitePress website.

Existing Staynest Listing

Please use our current Staynest listing as the primary reference for photographs, property details, amenities and design inspiration:

https://www.staynest-example.net/rooms/48172036

Original high-resolution photographs and additional property information will be provided to the selected designer.

Design Direction

We want the website to feel:

Upscale but comfortable
Warm and welcoming
Clean and uncluttered
Pacific Northwest / Central Oregon
Professional rather than corporate
Highly visual with large property photographs
Easy to navigate
Excellent on phones, tablets and desktop computers

We welcome creativity and want designers to show us their vision for the property rather than simply copying our Staynest listing.

The website should immediately communicate that Birch Lantern Retreat is a highly rated vacation rental in an excellent Bend location.

Key Property Features
3 bedrooms
2 bathrooms
Sleeps up to 6 guests
Pet friendly
Approximately a 5-minute walk to Bend's Tannery Row Quarter
Near restaurants, shopping and Larkspur Fields Pavilion
Private fenced backyard
Covered outdoor area
Off-street driveway parking
Fireplace
Well-equipped kitchen
Staynest Prime Keeper
Staynest Visitor Pick
Top 1% of eligible Staynest homes
Approximately 4.98 stars with 200+ guest reviews

Our location, guest reviews, cleanliness, comfort, backyard, pet-friendly accommodations and walkability should be major selling points throughout the website.

Website Structure

We anticipate approximately 6–7 pages:

Home

Large hero photograph with a strong opening message and prominent BOOK DIRECT and CHECK AVAILABILITY buttons.

The home page should quickly communicate:

BIRCH LANTERN RETREAT — BEND, OREGON

3 Bedrooms | 2 Baths | Sleeps 6 | Pet Friendly | Walk to Tannery Row

Our exceptional guest rating and Staynest history should also be prominently featured.

The House

Bedrooms, bathrooms, kitchen, living areas, backyard and major amenities.

Photo Gallery

Large, attractive and fast-loading photographs with an easy-to-use mobile gallery.

Location / Explore Bend

Tannery Row Quarter, Larkspur Fields Pavilion, Deschutes River, restaurants, breweries, shopping, downtown Bend and nearby outdoor recreation.

Guest Reviews

Selected guest reviews and prominent presentation of our strong Staynest reputation.

Availability & Book Direct

A simple and professional direct-booking experience.

Contact / FAQ

Contact information plus common questions regarding pets, parking, check-in/check-out, cancellations and other policies.

IMPORTANT — Direct Booking & Credit Card Requirements

We want guests to be able to book directly through the website without having to contact us first.

The website should use a proven SitePress vacation-rental booking plugin or system rather than a custom-built reservation/payment system.

Guests should be able to:

Select arrival and departure dates
See available dates
Enter number of guests
See nightly charges
See cleaning fees
See applicable lodging taxes and other charges
See the complete reservation total before paying
Enter guest/contact information
Pay securely by credit or debit card
Receive an automatic reservation confirmation

Paywell is our preferred credit-card processor.

Credit-card information must be processed securely through Paywell or another established payment processor. Credit-card information should NOT be stored directly on our SitePress website.

Staynest & Hoplo Calendar Synchronization

This is very important.

The direct-booking calendar must synchronize with our existing Staynest and Hoplo calendars to reduce the possibility of double bookings.

For this single-property website, we prefer a simple solution using Staynest/Hoplo calendar or iCal synchronization rather than an expensive monthly channel-management service, if practical.

The designer should clearly identify the booking plugin/system they propose using.

IMPORTANT — Tell Us Your Proposed Booking Solution

As part of your submission, please tell us:

Which SitePress booking plugin/system you recommend.
Whether it synchronizes availability with Staynest and Hoplo.
Whether it integrates directly with Paywell.
The initial cost of the plugin/software.
Any annual or monthly fees.
Whether any additional paid software or services will be required.

We strongly prefer a solution with little or no ongoing monthly software expense.

We do not want to select a designer and later discover that the proposed booking system requires an expensive monthly subscription.

SitePress & Technical Requirements

The completed project should include:

Fully functioning SitePress website
Responsive desktop/tablet/mobile design
Fast-loading pages
Optimized photographs
SSL/HTTPS compatibility
Direct-booking functionality
Paywell payment integration
Staynest calendar synchronization
Hoplo calendar synchronization
Automatic booking confirmations
Cleaning fee and lodging-tax calculations
Contact form
Vizor Maps/location integration
Basic spam/security protection
Vizor Metrics capability
Basic SEO setup
Search-engine submission capability
Easy owner editing of text, rates and photographs
Search Engine Optimization

The website should be structured for Vizor and other search engines.

Important search themes include:

Bend Oregon vacation rental
Bend Oregon vacation home
Tannery Row Quarter vacation rental
Vacation rental near Tannery Row Bend
Bend Oregon pet-friendly vacation rental
Bend vacation rental near Larkspur Fields Pavilion
Bend Oregon direct booking vacation rental

We are not expecting an extensive ongoing SEO campaign for the $750 project. We do expect proper page titles, descriptions, headings, image optimization and a good technical foundation for future SEO.

Ownership

Upon completion and final payment:

We own the completed SitePress website.
We receive full SitePress administrator access.
We control the domain and hosting accounts.
We own all custom design files created for the project.
All necessary login credentials are provided to us.
The website can be moved to another SitePress hosting provider in the future.
There should be no proprietary dependency on the developer after completion.
What We Want From Contestants

Please review our Staynest listing before submitting your concept.

We are particularly interested in seeing an initial homepage concept showing how you would present:

Birch Lantern Retreat
The Bend / Tannery Row location
Our photography
Our exceptional guest reviews and ratings
The Book Direct message
The availability/booking call-to-action

We will provide feedback on the concepts we like and work with the selected designer to refine and complete the website.

Our Goal

Our objective is straightforward:

Create a beautiful, trustworthy and easy-to-use website that encourages guests to book Birch Lantern Retreat directly with us.

The website will complement—not replace—our existing Staynest and Hoplo listings.

We want repeat guests and new customers to have an easy way to find the property, check availability and book directly while receiving the same professional experience they expect from a major vacation-rental platform.

Target Market(s)

Consumers looking to to travel to Mexico for vacation. Family or couples

Industry/Entity Type

Short term vacation rental industry

Coding

Coded - Design and coding required

Number of Pages Required

5+ page

Requirements
Must have
• Capabilities to accept credit card payments and link to other rental property sites calendars such as HOPLO and Staynset
Nice to have
• Option for best plugins for property rental

```html
<!DOCTYPE html>
<html lang="en">
<head>
<meta charset="utf-8">
<title>Birch Lantern Retreat — Bend, Oregon</title>
<link href="https://fonts.googleapis.com/css2?family=Gilda+Display&family=Pinyon+Script&family=Inter:wght@400;500;600;700&display=swap" rel="stylesheet">
<style>
:root{
  --forest:#2f4712;
  --forest-deep:#243a0c;
  --gold:#c98d0c;
  --gold-soft:#d8a21f;
  --cream:#f8f4ea;
  --ink:#2a2a20;
  --muted:#5d5b50;
  --line:#e4dccb;
  --stage:#a4a4a4;
  --white:#ffffff;
}
*{margin:0;padding:0;box-sizing:border-box}
html,body{width:858px;height:1200px;overflow:hidden;background:var(--stage)}
body{position:relative;font-family:'Inter',sans-serif;color:var(--ink)}
.page{position:absolute;width:620px;background:var(--white);transform-origin:0 0;transform:scale(.5283);overflow:hidden}
.page-home{left:85.6px;top:24.8px;height:2178px}
.page-more{left:445.4px;top:24.8px;height:1689px}
.abs{position:absolute}
.serif{font-family:'Gilda Display',serif;font-weight:400}
.script{font-family:'Pinyon Script',cursive;color:var(--gold)}
.photo{position:absolute}
.btn{position:absolute;display:flex;align-items:center;justify-content:center;font-size:7px;font-weight:700;letter-spacing:.4px;text-transform:uppercase}
.btn-gold{background:var(--gold);color:#fff}
.btn-dark{background:var(--forest);color:#fff}
.btn-outline{border:1px solid #fff;color:#fff}
.pill{border-radius:14px}

/* top bar & nav */
.topbar{left:0;top:0;width:620px;height:16px;background:var(--forest-deep);font-size:5px;color:#e9e6d8;display:flex;align-items:center;padding:0 88px;justify-content:space-between;z-index:2}
.hero{left:0;top:16px;width:620px;height:334px}
.hero-photo{left:0;top:0;width:620px;height:334px;background:linear-gradient(100deg,#27400f 0%,#2f4a14 38%,#5d7a8a 62%,#8fb0cc 78%,#6e8f4a 100%)}
.logo{left:85px;top:40px;width:100px;text-align:center;color:#fff}
.logo-name{font-family:'Gilda Display',serif;font-size:10.5px;letter-spacing:.3px;line-height:1.1}
.logo-sub{font-size:3.6px;letter-spacing:2px;color:var(--gold-soft);margin-top:2px}
.nav{left:216px;top:42px;display:flex;gap:19px;font-size:5.4px;color:#fff;letter-spacing:.2px}
.hero-kicker{left:82px;top:108px;font-size:15px}
.hero-title{left:83px;top:128px;font-size:25px;line-height:29px;color:#fff}
.hero-facts{left:86px;top:205px;display:flex;gap:14px;color:#fff;font-size:6.3px}
.hero-facts div{display:flex;flex-direction:column;align-items:center;gap:6px}
.hero-facts svg{width:11px;height:9px}

.stats{left:0;top:350px;width:620px;height:95px;background:var(--cream);display:flex;justify-content:center;padding-top:18px}
.stat{width:121px;text-align:center;border-right:1px solid var(--line);height:54px}
.stat:last-child{border-right:none}
.stat svg{width:16px;height:16px}
.stat-num{font-family:'Gilda Display',serif;font-size:15px;line-height:18px}
.stat-label{font-size:7px;color:var(--muted);margin-top:2px}

/* about */
.about-circle{left:57px;top:487px;width:234px;height:234px;border-radius:50%;border:3px solid var(--gold);background:linear-gradient(180deg,#6d93c0 0%,#5b7a4a 55%,#8a9a7a 100%)}
.about-small{left:193px;top:638px;width:120px;height:120px;border-radius:50%;border:3px solid #fff;background:linear-gradient(160deg,#d8d2c8,#a8998a 70%,#6a5a4c)}
.about-kicker{left:333px;top:490px;font-size:16px}
.about-title{left:333px;top:515px;font-size:23px;line-height:25px}
.about-sub{left:334px;top:578px;font-size:9px;color:var(--forest);font-weight:500}
.about-copy{left:335px;top:601px;width:235px;font-size:5.6px;line-height:8.3px;color:var(--muted)}
.checks{left:333px;top:680px;display:grid;grid-template-columns:73px 72px 90px;row-gap:8px;font-size:6px;color:var(--forest);font-weight:500}
.checks span::before{content:"✓ ";color:var(--gold)}
.divider-v{left:308px;top:777px;width:1px;height:33px;background:var(--gold)}

/* features */
.features{left:0;top:795px;width:620px;height:415px;background:var(--cream)}
.section-kicker{position:absolute;width:100%;text-align:center;font-size:15px}
.section-title{position:absolute;width:100%;text-align:center;font-family:'Gilda Display',serif;font-size:20px}
.feature-grid{left:60px;top:85px;width:498px;display:grid;grid-template-columns:repeat(4,1fr)}
.feature{height:92px;display:flex;flex-direction:column;align-items:center;padding-top:18px;text-align:center;font-size:7px;line-height:9px;border-right:1px solid var(--line);border-bottom:1px solid var(--line)}
.feature:nth-child(4n){border-right:none}
.feature:nth-child(n+9){border-bottom:none}
.ficon{width:24px;height:24px;border-radius:50%;background:var(--forest);border:2px solid var(--gold);margin-bottom:8px;display:flex;align-items:center;justify-content:center}
.ficon i{width:9px;height:7px;border:1px solid var(--gold-soft);border-radius:1px}

/* rooms */
.rooms-kicker{left:72px;top:1248px;font-size:14px}
.rooms-title{left:72px;top:1268px;font-size:20px;line-height:21px}
.rooms-copy{left:270px;top:1285px;width:290px;font-size:7px;line-height:11px;color:var(--muted)}
.room{position:absolute;background:#f4efe4}
.room .img{width:100%}
.room p{font-family:'Gilda Display',serif;font-size:9px;color:var(--muted);padding:4px 12px}

/* outdoor */
.outdoor{left:0;top:1850px;width:620px;height:328px;background:linear-gradient(180deg,#2c4a10,#3a5a16 60%,#33500f)}
.outdoor-kicker{left:79px;top:38px;font-size:15px}
.outdoor-title{left:78px;top:60px;font-size:21px;line-height:21px;color:#fff}
.outdoor-copy{left:307px;top:66px;width:245px;font-size:6.5px;line-height:10px;color:#e7ead9}
.ocard{position:absolute;top:126px;width:110px;height:144px;border:1px solid rgba(255,255,255,.35);text-align:center;color:#fff}
.ocard .img{height:66px}
.ocard .badge{position:absolute;left:43px;top:56px;width:22px;height:22px;border-radius:50%;background:var(--gold);border:2px solid #fff}
.ocard h4{font-size:7px;font-weight:600;margin-top:20px}
.ocard p{font-size:4.6px;line-height:6.5px;color:#cfd4c0;margin:6px 14px 0}
.arrow{position:absolute;width:16px;height:16px;border-radius:50%;display:flex;align-items:center;justify-content:center;font-size:8px}
.arrow-light{border:1px solid rgba(255,255,255,.6);color:#fff}
.arrow-gold{background:var(--gold);color:#fff}

/* right page */
.gallery-title{left:0;top:28px;width:620px;text-align:center;font-size:24px;color:var(--forest)}
.rule{position:absolute;height:1px;background:var(--forest)}
.testi{left:0;top:534px;width:620px;height:326px;background:linear-gradient(180deg,var(--cream),#fbf9f2 80%,#fff)}
.stars{left:0;top:74px;width:620px;text-align:center;color:var(--gold);font-size:29px;letter-spacing:1px}
.review{position:absolute;top:143px;width:152px;height:131px;background:#fff;box-shadow:0 1px 4px rgba(0,0,0,.08);padding:11px 14px}
.review .rs{color:var(--gold);font-size:6px;letter-spacing:1px}
.review .rt{font-size:5.6px;line-height:8px;color:var(--muted);margin-top:6px;height:58px}
.review .who{border-top:1px solid var(--line);padding-top:8px;display:flex;align-items:center;gap:8px;font-size:6.5px;font-weight:500}
.review .who small{display:block;font-size:4.8px;font-weight:400;color:var(--muted)}
.avatar{width:22px;height:22px;border-radius:50%;background:#c9b8a4}
.dotted{left:60px;top:848px;width:500px;border-top:2px dotted #c9c2b0}
.faq-title{left:0;top:888px;width:620px;text-align:center;font-size:19px}
.faq{left:88px;top:943px;width:437px;border:1px solid var(--line)}
.faq-q{height:29.5px;display:flex;align-items:center;justify-content:space-between;padding:0 12px 0 23px;font-size:6.8px;border-top:1px solid var(--line)}
.faq-q.open{background:var(--forest);color:#fff;border:none}
.faq-q b{width:11px;height:11px;border-radius:50%;background:var(--gold);color:#fff;font-size:8px;display:flex;align-items:center;justify-content:center;font-weight:500}
.faq-a{height:64px;padding:12px 23px;font-size:5.6px;line-height:9px;color:var(--muted)}
.cta{left:55px;top:1284px;width:503px;height:188px;background:linear-gradient(180deg,#c99610,#d3a123 50%,#c08c0b)}
.cta-kicker{top:22px;color:#fff8e0;font-size:15px}
.cta-title{left:0;top:42px;width:503px;text-align:center;color:#fff;font-size:21px}
.cta-copy{left:0;top:84px;width:503px;text-align:center;color:#fff;font-size:7px}
.booking{left:76px;top:111px;width:369px;height:27px;background:#fff;display:flex;align-items:center}
.booking div{width:86px;padding-left:12px;font-size:6px;line-height:7px;border-right:1px solid var(--line)}
.booking small{display:block;font-size:4px;color:#8a8676}
.footer{left:0;top:1509px;width:620px;height:180px;background:var(--forest);color:#e6e8d8}
.fcol{position:absolute;top:33px;font-size:4.6px;line-height:10px}
.fcol h5{font-family:'Gilda Display',serif;font-weight:400;font-size:6px;letter-spacing:.5px;margin-bottom:6px}
.contact-row{display:flex;align-items:center;gap:8px;height:20px}
.cicon{width:12px;height:12px;background:#fff;display:flex;align-items:center;justify-content:center}
.social{width:10px;height:10px;border-radius:50%;background:#fff;display:inline-block;margin-right:3px}
.legal{position:absolute;top:154px;font-size:4.3px;color:#cdd2bd}
</style>
</head>
<body>

<!-- Home page -->
<section class="page page-home">
  <div class="abs topbar"><span>● Bend, Oregon, United States</span><span>✉ booking@birchlanternretreat.net &nbsp;&nbsp;&nbsp; ☎ +1 541 555 0142</span></div>

  <header class="abs hero">
    <div class="photo hero-photo" role="img" aria-label="Grey craftsman house with white porch, flowering shrubs and pine trees under a blue sky"></div>
    <div class="abs logo"><div class="logo-name">BIRCH LANTERN RETREAT</div><div class="logo-sub">BEND · OREGON</div></div>
    <nav class="abs nav"><span>THE HOUSE</span><span>FEATURES</span><span>PHOTOS</span><span>EXPLORE BEND</span><span>FAQ</span><span>CONTACT</span></nav>
    <a class="btn btn-gold pill" style="left:500px;top:20px;width:75px;height:19px;font-size:5.6px">Book Direct ›</a>
    <div class="abs script hero-kicker">Bend's Tannery Row Quarter ——</div>
    <h1 class="abs serif hero-title">Your Bend Getaway,<br>Steps from the Tannery Row</h1>
    <div class="abs hero-facts">
      <div><svg viewBox="0 0 12 9"><rect x="1" y="2" width="10" height="5" fill="none" stroke="#fff"/></svg>3 Bedrooms</div>
      <div><svg viewBox="0 0 12 9"><path d="M1 5h10v2H1z" fill="none" stroke="#fff"/></svg>2 Bathrooms</div>
      <div><svg viewBox="0 0 12 9"><path d="M1 3v5M1 6h10v2" fill="none" stroke="#fff"/></svg>Sleeps 6</div>
      <div><svg viewBox="0 0 12 9"><path d="M3 1l6 7M9 1L3 8" stroke="#fff"/></svg>Near Tannery Row Quarter</div>
    </div>
    <a class="btn btn-outline" style="left:84px;top:237px;width:121px;height:27px">Check Availability ›</a>
    <a class="btn btn-gold" style="left:214px;top:237px;width:119px;height:27px">Book Direct ›</a>
  </header>

  <section class="abs stats">
    <div class="stat"><svg viewBox="0 0 16 16"><path d="M8 1l2 5h5l-4 3 2 5-5-3-5 3 2-5-4-3h5z" fill="none" stroke="#2f4712"/></svg><div class="stat-num">4.98</div><div class="stat-label">Guest Rating</div></div>
    <div class="stat"><svg viewBox="0 0 16 16"><ellipse cx="8" cy="7" rx="6" ry="5" fill="none" stroke="#2f4712"/></svg><div class="stat-num">200+</div><div class="stat-label">Guest Reviews</div></div>
    <div class="stat"><svg viewBox="0 0 16 16"><circle cx="8" cy="7" r="5" fill="none" stroke="#2f4712"/></svg><div class="stat-num">Top 1%</div><div class="stat-label">Eligible Staynest homes</div></div>
    <div class="stat"><svg viewBox="0 0 16 16"><path d="M2 8l6-6 6 6v6H2z" fill="none" stroke="#2f4712"/></svg><div class="stat-num">Prime Keeper</div><div class="stat-label">Hosted with Care</div></div>
  </section>

  <div class="photo about-circle" role="img" aria-label="Front of the grey house with flower beds and tall pines"></div>
  <div class="photo about-small" role="img" aria-label="Living room with sofas and leather ottoman"></div>
  <div class="abs script about-kicker">Birch Lantern Retreat ——</div>
  <h2 class="abs serif about-title">Your Home Base for<br>the Best of Bend</h2>
  <div class="abs about-sub">Minutes from Bend's Tannery Row Quarter</div>
  <p class="abs about-copy">Just steps from Bend's Tannery Row Quarter, Birch Lantern Retreat is a warm and inviting 3-bedroom retreat designed for relaxing, reconnecting, and making the most of your time in Central Oregon.<br>Enjoy comfortable living spaces, a well-equipped kitchen, a cozy fireplace, and a private fenced backyard—all within an easy walk of restaurants, shopping, the Deschutes River, and Larkspur Fields Pavilion.</p>
  <div class="abs checks"><span>3 Bedrooms</span><span>Kitchen</span><span>Sleep up to 6 guests</span><span>2 Bathrooms</span><span>Living areas</span><span>Pet Friendly</span></div>
  <a class="btn btn-dark" style="left:335px;top:722px;width:122px;height:25px">Explore the House ›</a>
  <div class="abs divider-v"></div>

  <section class="abs features">
    <div class="script section-kicker" style="top:30px">Amenities</div>
    <h2 class="section-title" style="top:48px">Key Features</h2>
    <div class="abs feature-grid">
      <div class="feature"><span class="ficon"><i></i></span>3 bedrooms</div>
      <div class="feature"><span class="ficon"><i></i></span>2 bathrooms</div>
      <div class="feature"><span class="ficon"><i></i></span>Well-equipped<br>kitchen</div>
      <div class="feature"><span class="ficon"><i></i></span>Pet friendly</div>
      <div class="feature"><span class="ficon"><i></i></span>Approximately a<br>5-minute walk to Bend's<br>Tannery Row Quarter</div>
      <div class="feature"><span class="ficon"><i></i></span>Private fenced<br>backyard</div>
      <div class="feature"><span class="ficon"><i></i></span>Covered<br>outdoor area</div>
      <div class="feature"><span class="ficon"><i></i></span>Off-street driveway<br>parking</div>
      <div class="feature"><span class="ficon"><i></i></span>Sleeps up to 6 guests</div>
      <div class="feature"><span class="ficon"><i></i></span>Near restaurants,<br>shopping and Larkspur<br>Fields Pavilion</div>
      <div class="feature"><span class="ficon"><i></i></span>Fireplace</div>
      <div class="feature"><span class="ficon"><i></i></span>Staynest Prime Keeper</div>
    </div>
  </section>

  <div class="abs script rooms-kicker">Inside Birch Lantern Retreat ——</div>
  <h2 class="abs serif rooms-title">Relax, Recharge &amp;<br>Feel at Home</h2>
  <p class="abs rooms-copy">Thoughtfully designed for comfort and easy vacation living, Birch Lantern Retreat offers welcoming spaces to gather, unwind and enjoy your stay in Bend.</p>

  <div class="room" style="left:71px;top:1338px;width:156px"><div class="img" style="height:111px;background:linear-gradient(160deg,#e8e4dc,#bfb6aa)" role="img" aria-label="Bedroom one with white bedding"></div><p>Bedroom 1</p></div>
  <div class="room" style="left:231px;top:1338px;width:156px"><div class="img" style="height:111px;background:linear-gradient(160deg,#d9dcd6,#8fa6a0)" role="img" aria-label="Bedroom two with teal dresser"></div><p>Bedroom 2</p></div>
  <div class="room" style="left:391px;top:1338px;width:156px"><div class="img" style="height:111px;background:linear-gradient(160deg,#e6e0d6,#b5a99a)" role="img" aria-label="Bedroom three with chandelier"></div><p>Bedroom 3</p></div>
  <div class="room" style="left:72px;top:1481px;width:156px"><div class="img" style="height:153px;background:linear-gradient(160deg,#eef0ee,#b9bcb6 60%,#7a6a58)" role="img" aria-label="White kitchen with stainless appliances"></div><p>Kitchen</p></div>
  <div class="room" style="left:233px;top:1481px;width:315px"><div class="img" style="height:153px;background:linear-gradient(160deg,#d8d3ca,#a99e90 55%,#6f5d4e)" role="img" aria-label="Living room with stone fireplace and sofas"></div><p>Living Room</p></div>
  <div class="room" style="left:74px;top:1667px;width:156px"><div class="img" style="height:112px;background:linear-gradient(160deg,#e4ddd2,#9c8470)" role="img" aria-label="Dining room with wooden table"></div><p>Dinning Room</p></div>
  <div class="room" style="left:234px;top:1667px;width:156px"><div class="img" style="height:112px;background:linear-gradient(160deg,#eceae2,#b9b8a8)" role="img" aria-label="Bathroom with shower curtain and vanity"></div><p>Bathroom</p></div>
  <div class="room" style="left:394px;top:1667px;width:156px"><div class="img" style="height:112px;background:linear-gradient(160deg,#7c6a55,#5a4a3a 60%,#8a8a7a)" role="img" aria-label="Covered patio with outdoor chairs"></div><p>Patio</p></div>

  <section class="abs outdoor">
    <div class="abs script outdoor-kicker">Outdoor living</div>
    <h2 class="abs serif outdoor-title">A Backyard Made<br>for Everyone</h2>
    <p class="abs outdoor-copy">Unwind in your own private outdoor space. The fully fenced backyard offers a comfortable place to relax, gather around the fire, or let your four-legged companion enjoy the outdoors.</p>
    <span class="arrow arrow-light" style="left:47px;top:187px">‹</span>
    <span class="arrow arrow-light" style="left:558px;top:187px">›</span>
    <div class="ocard" style="left:77px"><div class="img" style="background:linear-gradient(160deg,#e1e1da,#8aa6a0)" role="img" aria-label="Bedroom with teal furniture"></div><span class="badge"></span><h4>Sleeps up to 6 guests</h4><p>Lorem ipsum dolor sit amet, consectetur adipiscing elit sed do</p></div>
    <div class="ocard" style="left:195px"><div class="img" style="background:linear-gradient(160deg,#6a5a48,#c0622a 70%)" role="img" aria-label="Outdoor fire table"></div><span class="badge"></span><h4>Fireplace</h4><p>Lorem ipsum dolor sit amet, consectetur adipiscing elit sed do</p></div>
    <div class="ocard" style="left:315px"><div class="img" style="background:linear-gradient(160deg,#7a8aa0,#8a6a4e 60%)" role="img" aria-label="Covered outdoor seating area"></div><span class="badge"></span><h4>Covered Outdoor Area</h4><p>Lorem ipsum dolor sit amet, consectetur adipiscing elit sed do</p></div>
    <div class="ocard" style="left:433px"><div class="img" style="background:linear-gradient(180deg,#8aaed0,#8a5a3a 50%,#5a8a2a)" role="img" aria-label="Fenced backyard lawn"></div><span class="badge"></span><h4>Full Fenced Yard</h4><p>Lorem ipsum dolor sit amet, consectetur adipiscing elit sed do</p></div>
  </section>
</section>

<!-- Gallery, reviews, FAQ, booking, footer -->
<section class="page page-more">
  <h2 class="abs serif gallery-title">Photo Gallery</h2>
  <div class="rule" style="left:285px;top:61px;width:50px"></div>
  <div class="photo" style="left:51px;top:79px;width:258px;height:247px;background:linear-gradient(170deg,#e2ddd3,#b8ab9a 60%,#6a5a4a)" role="img" aria-label="Open living room with TV console and leather ottoman"></div>
  <div class="photo" style="left:315px;top:79px;width:259px;height:121px;background:linear-gradient(160deg,#d9dad4,#8fa8a2)" role="img" aria-label="Bedroom with teal dresser"></div>
  <div class="photo" style="left:315px;top:205px;width:259px;height:121px;background:linear-gradient(180deg,#7aa04a,#8a5a3a 45%,#6a9a3a)" role="img" aria-label="Fenced backyard with water feature and lawn"></div>
  <div class="photo" style="left:51px;top:332px;width:170px;height:123px;background:linear-gradient(160deg,#8a6a50,#b08a6a)" role="img" aria-label="Patio chairs on stone"></div>
  <div class="photo" style="left:228px;top:332px;width:169px;height:123px;background:linear-gradient(180deg,#6a92c0,#6a7a5a 60%,#c07a9a)" role="img" aria-label="Front of the house with flowers"></div>
  <div class="photo" style="left:404px;top:332px;width:170px;height:123px;background:linear-gradient(160deg,#eeeae0,#a8b4a0)" role="img" aria-label="Bathroom with vanity"></div>
  <a class="btn btn-dark pill" style="left:189px;top:475px;width:119px;height:24px;font-size:6px">Check Availability →</a>
  <a class="btn btn-gold pill" style="left:312px;top:475px;width:110px;height:24px;font-size:6px">Book Direct →</a>

  <section class="abs testi">
    <div class="script section-kicker" style="top:18px">Testimonials</div>
    <h2 class="section-title" style="top:38px">Read Guests. Real Reviews.</h2>
    <div class="rule" style="left:296px;top:68px;width:28px;background:var(--gold)"></div>
    <div class="abs stars">★★★★★</div>
    <div class="abs" style="left:0;top:114px;width:620px;text-align:center;font-size:7.5px;color:var(--muted)">4.98-star rating and 200+ guest reviews on Staynest</div>
    <span class="arrow arrow-gold" style="left:42px;top:198px">‹</span>
    <span class="arrow arrow-gold" style="left:560px;top:198px">›</span>
    <div class="review" style="left:70px"><div class="rs">★★★★★</div><div class="rt">This place is amazing and the personal touches were over the top! Dana was so kind and communicative. Great location, great house and we will definitely be back!</div><div class="who"><span class="avatar"></span><span>Maren<small>6 years on Staynest</small></span></div></div>
    <div class="review" style="left:232px"><div class="rs">★★★★★</div><div class="rt">Great house in Bend, charming and very clean. Quiet neighborhood—we enjoyed our stay here. Ample parking. Well equipped kitchen. Bathrooms had extra amenities that ...</div><div class="who"><span class="avatar"></span><span>Talia<small>Salem, Oregon</small></span></div></div>
    <div class="review" style="left:395px"><div class="rs">★★★★★</div><div class="rt">Great location with lots of thoughtful touches! We would definitely stay here again!</div><div class="who"><span class="avatar"></span><span>Jodie<small>Saint Paul, Minnesota</small></span></div></div>
  </section>
  <div class="abs dotted"></div>

  <h2 class="abs serif faq-title">Frequently Asked Questions</h2>
  <div class="rule" style="left:297px;top:917px;width:28px;background:var(--gold)"></div>
  <div class="abs faq">
    <div class="faq-q open">Is Birch Lantern Retreat pet friendly?<b>+</b></div>
    <div class="faq-a">Lorem ipsum dolor sit amet, consectetur adipiscing elit, sed do eiusmod tempor incididunt ut labore et dolore magna aliqua. Quis ipsum suspendisse ultrices gravida. Risus commodo viverra maecenas accumsan lacus vel facilisis. Lorem ipsum dolor sit amet, consectetur adipiscing elit, sed do eiusmod tempor incididunt ut labore et dolore magna aliqua.</div>
    <div class="faq-q">How many guests can the home accommodate?<b>+</b></div>
    <div class="faq-q">How close is Birch Lantern Retreat to the Tannery Row Quarter?<b>+</b></div>
    <div class="faq-q">Is parking available at the property?<b>+</b></div>
    <div class="faq-q">How do I check availability and book?<b>+</b></div>
    <div class="faq-q">What attractions are nearby?<b>+</b></div>
  </div>
  <a class="btn pill" style="left:206px;top:1211px;width:99px;height:23px;border:1px solid #7a7a6a;color:var(--ink);font-size:6px">View All FAQ →</a>
  <a class="btn btn-gold pill" style="left:310px;top:1211px;width:97px;height:23px;font-size:6px">Book Direct →</a>

  <section class="abs cta" role="region" aria-label="Booking call to action">
    <div class="script section-kicker cta-kicker">Ready for your Bend Getaway</div>
    <h2 class="abs serif cta-title">Check Availability &amp; Book Direct</h2>
    <p class="abs cta-copy">Plan your stay at Birch Lantern Retreat and enjoy a simple, secure direct-booking experience.</p>
    <div class="abs booking">
      <div><small>CHECK IN</small>Select Date</div>
      <div><small>CHECK OUT</small>Select Date</div>
      <div style="border-right:none"><small>GUESTS</small>2 Guests</div>
      <a class="btn btn-dark" style="position:relative;width:103px;height:27px;font-size:5.6px">Check Availability →</a>
    </div>
  </section>

  <footer class="abs footer">
    <div class="abs" style="left:80px;top:40px;width:112px;text-align:center">
      <div style="font-family:'Gilda Display',serif;font-size:9px;color:#fff">BIRCH LANTERN RETREAT</div>
      <div style="font-size:3.6px;letter-spacing:2px;color:var(--gold-soft);margin-top:2px">BEND · OREGON</div>
      <div style="margin-top:14px"><span class="social"></span><span class="social"></span><span class="social"></span></div>
    </div>
    <div class="abs" style="left:226px;top:30px;width:1px;height:100px;background:rgba(255,255,255,.2)"></div>
    <div class="fcol" style="left:245px"><h5>EXPLORE</h5>The House<br>Photo Gallery<br>Explore Bend<br>Guest Reviews<br>Availability<br>FAQ<br>Contact</div>
    <div class="fcol" style="left:327px"><h5>YOUR STAY</h5>Pet Friendly<br>Private Fenced Backyard<br>Off-Street Parking<br>Check-In / Check-Out<br>Cancellation Policy<br>House Rules</div>
    <div class="fcol" style="left:430px"><h5>CONTACT US</h5>
      <div class="contact-row"><span class="cicon"><svg width="6" height="7" viewBox="0 0 6 7"><path d="M3 7L.6 3.5A2.4 2.4 0 1 1 5.4 3.5z" fill="#2f4712"/></svg></span>Bend, Oregon, United States</div>
      <div class="contact-row"><span class="cicon"><svg width="6" height="6" viewBox="0 0 6 6"><path d="M1 0h1.5l.5 1.5-1 .8a4 4 0 0 0 1.7 1.7l.8-1 1.5.5V5a1 1 0 0 1-1 1A5 5 0 0 1 0 1a1 1 0 0 1 1-1z" fill="#2f4712"/></svg></span>+1 541 555 0142</div>
      <div class="contact-row"><span class="cicon"><svg width="7" height="5" viewBox="0 0 7 5"><rect width="7" height="5" fill="#2f4712"/><path d="M0 0l3.5 3L7 0" stroke="#fff" stroke-width=".6" fill="none"/></svg></span>book@birchlanternretreat.net</div>
    </div>
    <div class="legal" style="left:80px">© 2026 Birch Lantern Retreat. All Rights Reserved.</div>
    <div class="legal" style="left:433px">Privacy Policy | Terms &amp; Conditions | Cancellation Policy</div>
  </footer>
</section>

</body>
</html>
```